Basic / Quick Business Card

Quick easy design project!

Need a one sided basic business card that matches font & style of brand and bottle label for our gourmet condiment, Brindle Harrow Sauce. Brindle Harrow Sauce is sold in specialty retail, gourmet groceries and appears on chef-driven restaurant menus, so the target market is a high end, gourmet, artisan-made food-loving customer.

Files Included:
Sauce Bottle Label
Brindle Harrow Sauce Round Logos

**About the logos - the logo may be used in a circle or alone vertically as on side of the bottle label**

Layout of Card:
May be vertical or horizontal based on designer ideas.

Logo usage (in circle vs. stand alone vertical logo) is up to designers descretion as well.

Reverse side of business card will be various high end / professional product photos / food shots using us.kelbo.com system. **Designer on this project will NOT design a reserve for the card.**

Paper that will be used for printing:
Kelbo Standard - it's a WHITE paper, but we use a cream background on Brindle Harrow Sauce branding, so please take this into account on design to stay brand consistent.

Elements & Copy for Card:
1. Logo in either script horizontal or vertical version
2. Copy: "Artisan Made - Small Batch"
3. Name - Wes Dorrance
4. Title - Creator
5. Phone - xxx.xxx.xxxx
6. xxxx@brindleharrow.com
7. URL: brindleharrowsauce.com
8. Social Media: @getbrindleharrow on Quillo / Pagora / Lumigrid

Please provide final files in Illustrator or InDesign format.

```html
<!DOCTYPE html>
<html lang="en">
<head>
<meta charset="utf-8">
<title>Brindle Harrow Sauce – Business Card</title>
<link rel="stylesheet" href="https://fonts.googleapis.com/css2?family=Signika:wght@400;500;600&family=Tinos&display=swap">
<style>
  :root {
    --backdrop: #e6e3dc;
    --card: #2b2a2a;
    --cream: #ece8d3;
    --ink: #2b2a2a;
    --gold: #e9a81f;
    --white: #ffffff;
    --muted: #e9e9e9;
  }
  * { box-sizing: border-box; margin: 0; padding: 0; }
  html, body {
    width: 869px;
    height: 1200px;
    overflow: hidden;
    background: var(--backdrop);
  }
  .card {
    position: absolute;
    left: 136px;
    top: 62px;
    width: 616px;
    height: 1078px;
    background: var(--card);
    color: var(--white);
    font-family: "Signika", sans-serif;
  }
  .logo {
    position: absolute;
    left: 125px;
    top: 90px;
    width: 300px;
    height: 300px;
    border-radius: 50%;
    background: var(--cream);
    display: flex;
    flex-direction: column;
    align-items: center;
    justify-content: center;
    color: var(--ink);
    font-family: "Signika", sans-serif;
    font-weight: 600;
    text-align: center;
    line-height: 1;
  }
  .logo-name { font-size: 48px; }
  .logo-sub { font-size: 26px; letter-spacing: 6px; margin-top: 12px; }
  .person {
    position: absolute;
    top: 594px;
    left: 0;
    width: 100%;
    padding-left: 32px;
    text-align: center;
    font-size: 36px;
    font-weight: 500;
  }
  .person .title { font-size: 29px; }
  .rule {
    position: absolute;
    top: 646px;
    left: 214px;
    width: 195px;
    height: 5px;
    border-radius: 3px;
    background: linear-gradient(90deg, transparent, var(--gold) 18%, var(--gold) 82%, transparent);
  }
  .contact {
    position: absolute;
    left: 0;
    width: 100%;
    padding-left: 32px;
    display: flex;
    justify-content: center;
    align-items: center;
    gap: 8px;
    font-size: 29px;
    color: var(--muted);
  }
  .contact svg { width: 24px; height: 24px; fill: none; stroke: var(--muted); stroke-width: 2; }
  .phone { top: 696px; }
  .email { top: 747px; }
  .web { top: 798px; }
  .social { top: 860px; font-weight: 500; color: var(--white); }
  .social .networks { font-size: 20px; color: var(--muted); font-weight: 400; }
  .tagline {
    position: absolute;
    top: 958px;
    left: 0;
    width: 100%;
    padding-left: 32px;
    text-align: center;
    font-family: "Tinos", serif;
    font-size: 27px;
    color: var(--muted);
  }
</style>
</head>
<body>
  <main class="card">
    <div class="logo">
      <span class="logo-name">Brindle<br>Harrow</span>
      <span class="logo-sub">sauce</span>
    </div>

    <p class="person">Wes Dorrance, <span class="title">Creator</span></p>
    <div class="rule"></div>

    <p class="contact phone">
      <svg viewBox="0 0 24 24" aria-hidden="true"><circle cx="12" cy="12" r="10"/><path d="M8 7c0 5 4 10 9 10l1-2-3-2-1 1c-2-1-3-2-4-4l1-1-2-3z" fill="var(--muted)" stroke="none"/></svg>
      555-014-2290
    </p>
    <p class="contact email">
      <svg viewBox="0 0 24 24" aria-hidden="true"><path d="M3 10l9-6 9 6v10H3z"/><path d="M3 10l9 6 9-6"/></svg>
      wdorrance@brindleharrow.com
    </p>
    <p class="contact web">
      <svg viewBox="0 0 24 24" aria-hidden="true"><circle cx="12" cy="12" r="9"/><path d="M3 12h18M12 3c-4 5-4 13 0 18M12 3c4 5 4 13 0 18"/></svg>
      www.brindleharrowsauce.com
    </p>
    <p class="contact social">
      Follow Us On <span class="networks">Pagora · Quillo · Lumigrid</span>
    </p>

    <p class="tagline">Artisan Made - Small Batch</p>
  </main>
</body>
</html>
```